Need Business Card for our Real Estate Business with Sales Executive's Picture

PANTONE 484 C ( RED)

PANTONE 2766 C ( BLUE

Industry/Entity Type

Real Estate

Contact Information for Business Card

Name, Mobile, email, & picture of Person
Agency Phone, address, Web address

Requirements
Must have
• Our Logo Colours, Agent Picture,

```html
<!DOCTYPE html>
<html lang="en">
<head>
<meta charset="utf-8">
<title>Meridian Real Estate — Business Card</title>
<link href="https://fonts.googleapis.com/css2?family=EB+Garamond:wght@400;500&display=swap" rel="stylesheet">
<style>
  :root {
    --navy: #1b2459;
    --navy-deep: #141b47;
    --red: #9a3324;
    --paper: #fbfbfa;
    --ink-soft: #3c4262;
    --backdrop: #e6e3dd;
  }
  * { box-sizing: border-box; margin: 0; padding: 0; }
  html, body { width: 1200px; height: 886px; overflow: hidden; }
  body {
    background: var(--backdrop);
    font-family: "EB Garamond", Georgia, serif;
    position: relative;
  }
  .card {
    position: absolute;
    top: 293px;
    width: 520px;
    height: 300px;
    overflow: hidden;
    box-shadow: 0 6px 18px rgba(0,0,0,0.18);
  }
  /* Front */
  .card--front { left: 50px; background: var(--paper); color: var(--navy); }
  .brand { position: absolute; left: 40px; top: 46px; }
  .brand__row { display: flex; align-items: center; gap: 10px; }
  .brand__mark { width: 10px; height: 10px; background: var(--red); }
  .brand__name { font-size: 40px; letter-spacing: 3px; line-height: 1; color: var(--navy); }
  .brand__sub { font-size: 9px; letter-spacing: 3px; margin: 4px 0 0 66px; }
  .card__rule { position: absolute; left: 40px; top: 118px; width: 440px; height: 1px; background: var(--navy); }
  .person { position: absolute; right: 40px; top: 86px; text-align: right; }
  .person__name { font-size: 21px; letter-spacing: 1px; line-height: 1; }
  .person__title { font-size: 14px; color: var(--red); letter-spacing: 1px; margin-top: 12px; }
  .contacts { position: absolute; left: 40px; top: 148px; list-style: none; font-size: 12.5px; color: var(--ink-soft); line-height: 1.45; }
  .contacts li { display: flex; align-items: flex-start; gap: 10px; }
  .contacts svg { width: 10px; height: 10px; margin-top: 4px; flex: none; fill: var(--navy); }
  .contacts .gap { margin-top: 4px; }
  /* Back */
  .card--back { left: 630px; background: linear-gradient(135deg, var(--navy) 0%, var(--navy-deep) 100%); color: #fff; }
  .card--back .brand { left: 36px; top: 48px; }
  .card--back .brand__name { color: #fff; font-size: 44px; }
  .card--back .brand__sub { color: #fff; margin-left: 70px; }
  .web { position: absolute; left: 36px; top: 126px; font-size: 11px; letter-spacing: 5px; color: #fff; }
  .web-rule { position: absolute; left: 36px; top: 116px; width: 200px; height: 1px; background: rgba(255,255,255,0.7); }
  .portrait {
    position: absolute; right: 0; bottom: 0; width: 250px; height: 190px;
    background: linear-gradient(160deg, #2a3f8f 0%, #22367c 55%, #1a2a66 100%);
  }
</style>
</head>
<body>
  <section class="card card--front">
    <div class="brand">
      <div class="brand__row"><span class="brand__mark"></span><span class="brand__name">MERIDIAN</span></div>
      <div class="brand__sub">REAL ESTATE</div>
    </div>
    <div class="person">
      <div class="person__name">DANIEL REYES</div>
      <div class="person__title">CEO/FOUNDER</div>
    </div>
    <div class="card__rule"></div>
    <ul class="contacts">
      <li><svg viewBox="0 0 10 10"><path d="M5 0a3.5 3.5 0 0 0-3.5 3.5C1.5 6 5 10 5 10s3.5-4 3.5-6.5A3.5 3.5 0 0 0 5 0zm0 5a1.4 1.4 0 1 1 0-2.8A1.4 1.4 0 0 1 5 5z"/></svg><span>1420 Linden Court<br>Fairbanks, Alaska 99701</span></li>
      <li class="gap"><svg viewBox="0 0 10 10"><path d="M2 0l2 2.5-1 1.2a6 6 0 0 0 3.3 3.3l1.2-1L10 8 8.5 10C4 10 0 6 0 1.5z"/></svg><span>555 210 4187</span></li>
      <li><svg viewBox="0 0 10 10"><rect x="2.5" y="0" width="5" height="10" rx="1"/></svg><span>555 318 7720</span></li>
      <li><svg viewBox="0 0 10 10"><path d="M0 2h10v6H0zM0 2l5 3.5L10 2" stroke="#fbfbfa" stroke-width="0.8"/></svg><span>daniel@meridian.com</span></li>
      <li><svg viewBox="0 0 10 10"><circle cx="5" cy="5" r="5"/></svg><span>www.meridian.com</span></li>
    </ul>
  </section>

  <section class="card card--back">
    <div class="brand">
      <div class="brand__row"><span class="brand__mark"></span><span class="brand__name">MERIDIAN</span></div>
      <div class="brand__sub">REAL ESTATE</div>
    </div>
    <div class="web-rule"></div>
    <div class="web">www.meridian.com</div>
    <div class="portrait" role="img" aria-label="Portrait photo of the sales executive in a blue suit"></div>
  </section>
</body>
</html>
```